Electrical contractor Brochure design

We are looking a elegant brochure design for our new branding campaign. Logo ai file is attached. We mainly work in power plants and manufacturing facilities. We would like some pictures to show those types of facilities.

Target Market(s)

Industrial commercial electrician

Industry/Entity Type

Contractor

Font styles to use
Sans Serif

```html
<!DOCTYPE html>
<html lang="en">
<head>
<meta charset="utf-8">
<title>Halden Electric Brochure</title>
<link href="https://fonts.googleapis.com/css2?family=Michroma&family=Open+Sans:wght@400;600;700&display=swap" rel="stylesheet">
<style>
  :root{
    --bg:#9a9a9a;
    --red:#a5102c;
    --red-dark:#7d0a20;
    --ink:#161616;
    --paper:#f4f4f4;
    --white:#ffffff;
    --muted:#e8c9cf;
  }
  *{margin:0;padding:0;box-sizing:border-box}
  html,body{width:1200px;height:788px;overflow:hidden;background:var(--bg)}
  body{font-family:"Open Sans",Arial,sans-serif;color:var(--white)}
  .spread{position:absolute;left:40px;top:24px;width:1120px;height:740px;box-shadow:0 8px 24px rgba(0,0,0,.35)}
  .spread-art{position:absolute;inset:0}
  .text{position:absolute}
  .about{left:40px;top:150px;width:300px}
  .about h2{font-family:"Michroma",Arial,sans-serif;font-size:24px;font-weight:400;line-height:1}
  .rule{display:block;width:120px;height:3px;background:var(--white);margin:8px 0 10px}
  .about p{font-size:10.5px;line-height:1.45}
  .brand{display:flex;align-items:center;gap:8px;font-family:"Open Sans",Arial,sans-serif;font-weight:700;font-size:20px;color:var(--white)}
  .brand-dot{width:22px;height:22px;border-radius:50%;background:var(--white)}
  .back-brand{left:300px;top:440px}
  .contact{left:300px;top:480px;width:250px}
  .contact h3{font-family:"Michroma",Arial,sans-serif;font-weight:400;font-size:15px}
  .contact .rule{width:150px;margin:6px 0 8px}
  .contact ul{list-style:none;font-size:11.5px;line-height:1.75}
  .contact li{display:flex;align-items:center;gap:7px}
  .ico{width:11px;height:11px;flex:none}
  .social{display:flex;gap:5px;margin-top:6px}
  .social span{width:14px;height:14px;border-radius:50%;border:1.5px solid var(--white)}
  .headline{left:610px;top:300px;width:440px}
  .headline h1{font-family:"Michroma",Arial,sans-serif;font-weight:400;font-size:27px;line-height:1.2}
  .headline .sub{font-family:"Michroma",Arial,sans-serif;font-size:12px;margin-top:4px}
  .headline .rule{width:200px;margin:6px 0 14px}
  .headline p{font-size:11px;line-height:1.5;width:300px}
  .front-brand{left:770px;top:640px}
  .vertical-url{left:1070px;top:20px;writing-mode:vertical-rl;font-size:12px;font-weight:600;color:var(--ink);letter-spacing:.5px}
</style>
</head>
<body>
<main class="spread">
  <svg class="spread-art" width="1120" height="740" viewBox="0 0 1120 740" xmlns="http://www.w3.org/2000/svg">
    <defs>
      <linearGradient id="back-red" x1="0" y1="0" x2="1" y2="1">
        <stop offset="0" stop-color="#b0132f"/><stop offset="1" stop-color="#850a22"/>
      </linearGradient>
      <linearGradient id="night-plant" x1="0" y1="0" x2="0" y2="1">
        <stop offset="0" stop-color="#1c2a66"/><stop offset=".6" stop-color="#3d4f8a"/><stop offset="1" stop-color="#2a2620"/>
      </linearGradient>
      <linearGradient id="dusk-plant" x1="0" y1="0" x2="0" y2="1">
        <stop offset="0" stop-color="#2f4a66"/><stop offset=".55" stop-color="#b8843a"/><stop offset="1" stop-color="#1c1710"/>
      </linearGradient>
      <linearGradient id="workers" x1="0" y1="0" x2="1" y2="1">
        <stop offset="0" stop-color="#9aa6b4"/><stop offset="1" stop-color="#2e3a5a"/>
      </linearGradient>
      <linearGradient id="fold" x1="0" y1="0" x2="1" y2="0">
        <stop offset="0" stop-color="#000" stop-opacity="0"/><stop offset=".5" stop-color="#000" stop-opacity=".18"/><stop offset="1" stop-color="#000" stop-opacity="0"/>
      </linearGradient>
      <clipPath id="spread-clip"><rect width="1120" height="740"/></clipPath>
      <clipPath id="front-clip"><rect x="560" width="560" height="740"/></clipPath>
      <clipPath id="front-circle"><circle cx="790" cy="470" r="290"/></clipPath>
    </defs>
    <g clip-path="url(#spread-clip)">
      <rect class="back-page" width="560" height="740" fill="url(#back-red)"/>
      <rect class="front-page" x="560" width="560" height="740" fill="var(--paper)"/>
      <g clip-path="url(#front-clip)">
        <circle class="front-red-disc" cx="790" cy="470" r="290" fill="var(--red)"/>
        <rect class="front-black-band" x="560" y="610" width="560" height="130" fill="var(--ink)" clip-path="url(#front-circle)"/>
      </g>
      <circle cx="560" cy="160" r="228" fill="none" stroke="var(--white)" stroke-width="2"/>
      <g role="img" aria-label="Photo: power plant chimneys lit at night">
        <circle cx="560" cy="160" r="215" fill="url(#night-plant)"/>
      </g>
      <circle cx="150" cy="610" r="212" fill="none" stroke="var(--white)" stroke-width="2"/>
      <g role="img" aria-label="Photo: power station with cooling towers at dusk">
        <circle cx="150" cy="610" r="200" fill="url(#dusk-plant)"/>
      </g>
      <g role="img" aria-label="Photo: electricians working on industrial equipment">
        <circle cx="330" cy="365" r="72" fill="url(#workers)" stroke="var(--white)" stroke-width="4"/>
      </g>
      <rect x="520" width="80" height="740" fill="url(#fold)"/>
    </g>
  </svg>

  <section class="text about">
    <h2>About us</h2><span class="rule"></span>
    <p>Lorem ipsum dolor sit amet, consectetur adipiscing elit. Vestibulum dignissim, ante in faucibus volutpat, nisi augue consequat sem, sit amet dapibus purus neque sed ipsum. Cras quis elementum leo. Maecenas gravida pellentesque lacus at consequat. Aliquam pellentesque malesuada fringilla.</p>
  </section>

  <div class="text brand back-brand"><span class="brand-dot"></span>Halden Electric</div>

  <section class="text contact">
    <h3>GET IN TOUCH</h3><span class="rule"></span>
    <ul>
      <li><svg class="ico" viewBox="0 0 12 12"><path d="M6 1a3.5 3.5 0 0 0-3.5 3.5C2.5 7.5 6 11 6 11s3.5-3.5 3.5-6.5A3.5 3.5 0 0 0 6 1z" fill="#fff"/></svg>PO Box 14 Brookfield, OH 44403</li>
      <li><svg class="ico" viewBox="0 0 12 12"><path d="M3 1l2 2.5-1 1.3a6 6 0 0 0 3.2 3.2l1.3-1L11 9l-1 2C5 11 1 7 1 2z" fill="#fff"/></svg>555-214-0187</li>
      <li><svg class="ico" viewBox="0 0 12 12"><rect x="1" y="2.5" width="10" height="7" fill="none" stroke="#fff"/><path d="M1 2.5l5 4 5-4" fill="none" stroke="#fff"/></svg>info@halden-electric.com</li>
      <li><svg class="ico" viewBox="0 0 12 12"><circle cx="6" cy="6" r="4.8" fill="none" stroke="#fff"/><path d="M1.2 6h9.6M6 1.2c-2 2.6-2 7 0 9.6M6 1.2c2 2.6 2 7 0 9.6" fill="none" stroke="#fff" stroke-width=".8"/></svg>www.halden-electric.com</li>
    </ul>
    <div class="social"><span></span><span></span><span></span><span></span><span></span><span></span></div>
  </section>

  <section class="text headline">
    <h1>LOREM IPSUM<br>DOLOR SIT AMET</h1>
    <div class="sub">Consectetur Adipiscing Elit</div><span class="rule"></span>
    <p>Lorem ipsum dolor sit amet, consectetur adipiscing elit. Vestibulum dignissim, ante in faucibus volutpat, nisi augue consequat sem, sit amet dapibus purus neque sed ipsum. Cras quis elementum leo. Maecenas gravida pellentesque lacus at consequat. Aliquam pellentesque malesuada fringilla.</p>
  </section>

  <div class="text brand front-brand"><span class="brand-dot"></span>Halden Electric</div>
  <div class="text vertical-url">www.halden-electric.com</div>
</main>
</body>
</html>
```